Modern Business Card For A Digital Advertising Company

I'll be print on the Pell Prints Velour paper http://us.pellprints.com/products/velour/business-cards.html
Need's to be modern and use the color palette of the logo or gray scales. I think integrating the pixelation of the logo in to the card and having it wrap from one side to the other could be interesting. My company provides ad operations, web development, and number of other services to websites around the world. You can see my website at http://www.zantorhq.com
Contact info on the card needs to have
Owen Lasko
President
p.318.204.6637
owen@zantorhq.com
http://www.zantorhq.com
Doesn't necessarily need to be in that order
Website owners
Business

```html
<!DOCTYPE html>
<html lang="en">
<head>
<meta charset="utf-8">
<title>Zantor HQ — Business Card</title>
<link rel="stylesheet" href="https://fonts.googleapis.com/css2?family=Arimo:ital,wght@0,400;0,700;1,400&display=swap">
<style>
  :root {
    --backdrop: #2b2b2b;
    --card: #ffffff;
    --brand-green: #8cc63f;
    --name-green: #5e8f2f;
    --ink: #3a3a3a;
    --ink-soft: #444444;
    --rule: #333333;
  }
  * { margin: 0; padding: 0; box-sizing: border-box; }
  html, body { width: 1200px; height: 450px; overflow: hidden; }
  body {
    background: var(--backdrop);
    font-family: "Arimo", Arial, sans-serif;
    position: relative;
  }
  .card {
    position: absolute;
    top: 78px;
    width: 525px;
    height: 300px;
    background: var(--card);
  }
  .card--front { left: 58px; }
  .card--back { left: 622px; }

  /* Front */
  .brand-mark {
    position: absolute;
    left: 84px;
    top: 136px;
    width: 160px;
    display: flex;
    align-items: center;
    gap: 8px;
    white-space: nowrap;
  }
  .brand-mark__square {
    width: 18px;
    height: 18px;
    flex: none;
    background: var(--brand-green);
  }
  .brand-mark__name {
    font-size: 20px;
    font-weight: 700;
    color: var(--brand-green);
    letter-spacing: 0.5px;
  }
  .divider {
    position: absolute;
    left: 262px;
    top: 39px;
    width: 1.5px;
    height: 223px;
    background: var(--rule);
  }
  .person {
    position: absolute;
    left: 297px;
    top: 72px;
  }
  .person__name {
    font-size: 21px;
    font-weight: 700;
    color: var(--name-green);
    line-height: 1.1;
  }
  .person__role {
    font-size: 17px;
    color: var(--ink);
    line-height: 1.15;
  }
  .contact {
    position: absolute;
    left: 296px;
    top: 172px;
    list-style: none;
  }
  .contact__item {
    display: flex;
    align-items: center;
    gap: 5px;
    font-size: 15.5px;
    color: var(--ink);
    height: 23.5px;
  }
  .contact__icon { width: 12px; height: 12px; flex: none; }

  /* Back */
  .back-mark {
    position: absolute;
    left: 0;
    right: 0;
    top: 110px;
    display: flex;
    justify-content: center;
    align-items: center;
    gap: 12px;
  }
  .back-mark__square {
    width: 30px;
    height: 30px;
    background: var(--brand-green);
  }
  .back-mark__name {
    font-size: 34px;
    font-weight: 700;
    color: var(--brand-green);
    letter-spacing: 1px;
  }
  .back-url {
    position: absolute;
    left: 0; right: 0;
    top: 186px;
    text-align: center;
    font-size: 14.5px;
    letter-spacing: 2.4px;
    color: var(--ink-soft);
  }
  .back-url__domain { color: var(--brand-green); font-weight: 700; }
  .services {
    position: absolute;
    left: 0; right: 0;
    top: 233px;
    text-align: center;
    font-size: 14.5px;
    font-style: italic;
    letter-spacing: 0.9px;
    line-height: 18px;
    color: var(--ink);
  }
</style>
</head>
<body>
  <section class="card card--front">
    <div class="brand-mark">
      <span class="brand-mark__square"></span>
      <span class="brand-mark__name">ZANTOR HQ</span>
    </div>
    <div class="divider"></div>
    <div class="person">
      <p class="person__name">Owen Lasko</p>
      <p class="person__role">President</p>
    </div>
    <ul class="contact">
      <li class="contact__item">
        <svg class="contact__icon" viewBox="0 0 12 12" aria-hidden="true"><circle cx="6" cy="6" r="5.3" fill="none" stroke="#8cc63f" stroke-width="1.2"/><path d="M4 3.2 L5.2 4.6 L4.6 5.4 Q5.4 7 6.8 7.6 L7.5 7 L8.8 8.1 L8 9 Q5 8.6 3.2 4.2 Z" fill="#8cc63f"/></svg>
        <span>318.204.6637</span>
      </li>
      <li class="contact__item">
        <svg class="contact__icon" viewBox="0 0 12 12" aria-hidden="true"><rect x="1" y="3" width="10" height="7" fill="#8cc63f"/><path d="M1 3 L6 7 L11 3" fill="none" stroke="#fff" stroke-width="1"/></svg>
        <span>owen@zantorhq.com</span>
      </li>
      <li class="contact__item">
        <svg class="contact__icon" viewBox="0 0 12 12" aria-hidden="true"><circle cx="6" cy="6" r="5" fill="#8cc63f"/><path d="M1 6 H11 M6 1 V11" stroke="#fff" stroke-width="0.9"/></svg>
        <span>www.zantorhq.com</span>
      </li>
    </ul>
  </section>

  <section class="card card--back">
    <div class="back-mark">
      <span class="back-mark__square"></span>
      <span class="back-mark__name">ZANTOR HQ</span>
    </div>
    <p class="back-url">www.<span class="back-url__domain">zantorhq</span>.com</p>
    <p class="services">Ad Operations, Web Development, Hosting,Site Speed<br>Social Media, Search Engine Optimization</p>
  </section>
</body>
</html>
```